Website for my law practice

I am a solo practitioner, who specializes in family law and estate planning in Massachusetts. I need to re-do my website, as it is outdated. I like the idea of a nontraditional law firm website. My website address is: doloresquintanalaw.com. I would like to retain my logo in the green color, as part of the new website. I have uploaded my logo below.

My hourly rate has changed from what is listed on my current website. My new hourly rate is $385.00. Please use this hourly rate when creating the website.

Good morning,

I have reviewed the designs submitted so far. I am happy that the "dq" logo in the green color is part of each of the designs submitted. I am also happy that the standard items seen in law firm websites, such as the scales of justice, etc. were not incorporated. Although the green logo is great, I do not think rest of the website has to have the same green color throughout. Additionally, I was hoping for something more creative, to make the website standout and not the stock web designs you see everyday. Please incorporate more unique images if you can. For example of what I mean, please look at this website: https://www.rosalindfenwicklaw.com

```html
<!DOCTYPE html>
<html lang="en">
<head>
<meta charset="utf-8">
<title>Dolores Quintana — Attorney at Law</title>
<link href="https://fonts.googleapis.com/css2?family=Poppins:wght@300;400;500;600&display=swap" rel="stylesheet">
<style>
:root{
  --green:#2f8f1f;
  --navy:#1e2b3a;
  --navy-soft:#2c3e53;
  --clay:#c46f45;
  --clay-soft:#e9c2a8;
  --sand:#f6efe5;
  --sand-deep:#eadcc8;
  --ink:#24282e;
  --body:#4d4f53;
  --line:#d8ccbb;
  --white:#ffffff;
}
*{box-sizing:border-box;margin:0;padding:0}
html,body{width:1200px;height:4902px;overflow:hidden}
body{position:relative;font-family:'Poppins',sans-serif;color:var(--body);background:var(--white)}
.abs{position:absolute}
.btn{position:absolute;display:inline-flex;align-items:center;gap:8px;height:42px;padding:0 22px;border-radius:21px;font-size:15px;font-weight:500;text-decoration:none;letter-spacing:.2px;white-space:nowrap}
.btn-solid{background:var(--clay);color:var(--white)}
.btn-ghost{border:2px solid var(--white);color:var(--white)}
.btn svg{width:12px;height:12px}

/* header */
.site-header{position:absolute;left:0;top:0;width:1200px;height:143px;background:var(--white)}
.brand{position:absolute;left:64px;top:52px;display:flex;align-items:center;gap:10px}
.brand-dot{width:36px;height:36px;border:3px solid var(--green);border-radius:50%}
.brand-name{color:var(--green);font-size:12px;font-weight:600;line-height:14px}
.call{position:absolute;right:62px;top:22px;display:flex;align-items:center;gap:8px;font-size:14px;color:var(--ink)}
.call b{color:var(--clay);font-weight:500}
.call-icon{width:34px;height:34px;border:2px solid var(--clay);border-radius:50%;display:flex;align-items:center;justify-content:center}
.nav{position:absolute;right:62px;top:72px;display:flex;align-items:center;gap:48px;font-size:13px;color:var(--ink)}
.nav .active{color:var(--clay);border-bottom:2px solid var(--clay);padding-bottom:6px}
.nav .cta{background:var(--navy);color:var(--white);padding:5px 22px;border-radius:14px}

/* hero */
.hero-photo{position:absolute;left:0;top:143px;width:1200px;height:827px;background:linear-gradient(110deg,#c48d66 0%,#e9d7c6 30%,#f3efe8 55%,#dfe6ea 80%,#c9ced2 100%)}
.hero-ring{position:absolute;left:262px;top:98px;width:678px;height:678px;border-radius:50%;border:2px solid rgba(255,255,255,.7)}
.hero-circle{position:absolute;left:278px;top:114px;width:646px;height:646px;border-radius:50%;background:rgba(30,43,58,.84)}
.hero-accent{position:absolute;left:820px;top:150px;width:90px;height:90px;border-radius:50%;background:var(--clay)}
.hero-text{position:absolute;left:278px;width:646px;text-align:center;color:var(--white)}
.hero-lead{font-size:24px;font-weight:400;line-height:38px}
.hero-title{font-size:52px;font-weight:400;line-height:66px}
.hero-curve{position:absolute;left:0;top:780px}

/* about */
.about-frame{position:absolute;left:160px;top:1084px;width:306px;height:420px;background:var(--white);box-shadow:0 4px 18px rgba(0,0,0,.18);border-radius:10px}
.about-offset{position:absolute;left:136px;top:1060px;width:306px;height:420px;border-radius:10px;background:var(--sand-deep)}
.about-photo{position:absolute;left:168px;top:1092px;width:290px;height:404px;border-radius:8px;background:linear-gradient(160deg,#8a7a64,#c9b08e 45%,#9a917f)}
.badge{position:absolute;left:364px;top:1388px;width:82px;height:96px;background:#f7f4ea;border:2px solid #d8c27a}
.h2{position:absolute;font-size:44px;font-weight:300;color:var(--ink);letter-spacing:.5px;white-space:nowrap}
.h2-sm{font-size:33px}
.kicker{position:absolute;font-size:19px;font-weight:600;color:var(--clay);display:flex;align-items:center;gap:12px;white-space:nowrap}
.kicker i{display:block;width:42px;height:2px;background:var(--green)}
.para{position:absolute;font-size:13px;line-height:24px;text-align:justify;color:var(--body)}

/* consultation */
.pale-band{position:absolute;left:0;top:1806px;width:1200px;height:733px;background:var(--sand)}
.consult{position:absolute;left:68px;top:1597px;width:1067px;height:324px;border-radius:24px;background:var(--navy);overflow:hidden}
.consult-arc{position:absolute;border-radius:50%;border:2px solid rgba(255,255,255,.08)}
.consult h3{position:absolute;top:52px;width:100%;text-align:center;font-size:33px;font-weight:400;color:var(--white)}
.consult h3::after{content:"";display:block;width:60px;height:2px;background:var(--clay);margin:14px auto 0}
.consult p{position:absolute;top:140px;left:60px;right:60px;text-align:center;font-size:13px;line-height:24px;color:#e6e9ee}

/* family */
.photo-ring{position:absolute;border:2px solid var(--clay);border-radius:50%}
.photo-fill{position:absolute;border-radius:50%}
.family-fill{background:linear-gradient(140deg,#4a2a8a,#6f4fb5 40%,#d8d8d8 60%,#c7c7c7)}
.estate-fill{background:linear-gradient(160deg,#1c2a54,#2c3f78 50%,#a9a6a0 80%,#d6d2ca)}
.services{position:absolute;left:167px;top:2465px;width:868px;height:131px;background:var(--clay);border-radius:12px;box-shadow:0 8px 20px rgba(196,111,69,.3)}
.service{position:absolute;top:28px;display:flex;align-items:center;gap:14px;color:var(--white);font-size:15px;white-space:nowrap}
.service-icon{width:76px;height:76px;border-radius:50%;background:var(--white);display:flex;align-items:center;justify-content:center}

/* estate list */
.estate-card{position:absolute;left:148px;top:3157px;width:898px;height:286px;background:var(--white);border-radius:24px;box-shadow:0 4px 28px rgba(30,43,58,.1);border-top:4px solid var(--clay)}
.doc{position:absolute;display:flex;align-items:center;gap:12px;font-size:13px;color:var(--body);line-height:15px;white-space:nowrap}
.doc-icon{width:40px;height:40px;border-radius:50%;background:var(--navy);display:flex;align-items:center;justify-content:center;flex:none}

/* faq */
.faq-q{position:absolute;left:67px;width:637px;font-size:15px;font-weight:600;color:var(--ink);line-height:18px}
.faq-q .num{color:var(--clay);margin-right:8px}
.faq-q.open{color:var(--navy)}
.faq-toggle{position:absolute;right:0;top:0;width:16px;height:16px;border-radius:50%;background:var(--navy)}
.faq-q.open .faq-toggle{background:var(--clay)}
.faq-line{position:absolute;left:67px;width:637px;height:1px;background:var(--line)}
.faq-answer{position:absolute;left:95px;top:3748px;width:609px;font-size:13px;line-height:24px;text-align:justify}
.faq-answer em{font-style:normal;color:var(--clay);font-weight:500}
.faq-back{position:absolute;left:815px;top:3630px;width:325px;height:433px;border-radius:14px;background:var(--sand-deep)}
.faq-photo{position:absolute;left:793px;top:3608px;width:325px;height:433px;border-radius:14px;background:linear-gradient(160deg,#3a3a3a,#9a9a9a 50%,#5b5b5b)}

/* contact */
.contact-wave{position:absolute;left:0;top:4280px}
.contact-box{position:absolute;left:68px;top:4169px;width:1067px;height:453px;border-radius:24px;overflow:hidden;background:linear-gradient(180deg,var(--sand) 0%,var(--sand) 30%,var(--sand-deep) 30%,var(--sand-deep) 100%)}
.contact-photo{position:absolute;left:0;top:0;width:468px;height:453px;background:linear-gradient(180deg,#eef3f0 0%,#cfdccf 45%,#8fa884 100%)}
.contact-box h2{position:absolute;left:506px;top:40px;font-size:46px;font-weight:400;color:var(--ink)}
.field{position:absolute;background:var(--white);border:1px solid var(--line);font-size:13px;color:#777;padding:12px 20px}

/* footer */
.footer-title{position:absolute;font-size:16px;font-weight:500;color:var(--white)}
.footer-links{position:absolute;left:232px;top:4716px;list-style:none;font-size:13px;color:var(--white)}
.footer-links li{display:flex;align-items:center;gap:8px;height:28px}
.footer-links li::before{content:"";width:8px;height:8px;border:1.5px solid var(--clay-soft);border-radius:50%}
.footer-brand{position:absolute;left:450px;top:4660px;width:300px;text-align:center;color:var(--white)}
.footer-mark{width:90px;height:90px;border:5px solid var(--white);border-radius:50%;margin:0 auto 16px}
.footer-brand p{font-size:22px;font-weight:600;line-height:28px}
.fcontact{position:absolute;left:833px;display:flex;gap:14px;align-items:center;font-size:11px;line-height:14px;color:var(--white)}
.fcontact-icon{width:26px;height:26px;border:1.5px solid var(--clay-soft);display:flex;align-items:center;justify-content:center;flex:none}
.footer-rule{position:absolute;left:68px;top:4868px;width:1067px;height:1px;background:rgba(255,255,255,.35)}
.copyright{position:absolute;top:4876px;width:1200px;text-align:center;font-size:12px;color:var(--white)}
</style>
</head>
<body>

<header class="site-header">
  <div class="brand"><span class="brand-dot"></span><span class="brand-name">Dolores Quintana<br>Attorney at Law</span></div>
  <div class="call">
    <span class="call-icon"><svg width="16" height="16" viewBox="0 0 24 24" fill="none" stroke="#c46f45" stroke-width="2"><path d="M5 3h4l2 5-3 2a12 12 0 006 6l2-3 5 2v4a2 2 0 01-2 2A18 18 0 013 5a2 2 0 012-2z"/></svg></span>
    <b>CALL US :</b> (555)014-2290
  </div>
  <nav class="nav">
    <span class="active">HOME</span><span>FAMILY LAW</span><span>ESTATE PLANNING</span><span>ABOUT</span><span>LOCATION</span><span>FAQ</span><span class="cta">CONTACT</span>
  </nav>
</header>

<section class="hero-photo" role="img" aria-label="Photo of an attorney consulting with a smiling couple at a bright office table">
  <div class="hero-ring"></div>
  <div class="hero-circle"></div>
  <div class="hero-accent"></div>
  <p class="hero-text hero-lead" style="top:266px">Dolores Quintana is a Solo Practitioner<br>focusing her practice on matters pertaining to</p>
  <h1 class="hero-text hero-title" style="top:350px">FAMILY LAW AND<br>ESTATE PLANNING.</h1>
  <a class="btn btn-ghost" style="left:510px;top:526px;height:46px">CONTACT US <svg viewBox="0 0 12 12" fill="none" stroke="#fff" stroke-width="1.5"><path d="M2 10L10 2M4 2h6v6"/></svg></a>
</section>
<svg class="hero-curve" width="1200" height="200" viewBox="0 0 1200 200">
  <path d="M0 40 Q600 300 1200 40 L1200 200 L0 200Z" fill="#f6efe5"/>
  <path d="M0 70 Q600 300 1200 70 L1200 200 L0 200Z" fill="#e9c2a8"/>
  <path d="M0 60 Q600 250 1200 20 L1200 200 L0 200Z" fill="#fff"/>
  <path d="M0 100 Q600 260 1200 80" stroke="#eadcc8" stroke-width="3" fill="none"/>
</svg>

<section class="about">
  <div class="about-offset"></div>
  <div class="about-frame"></div>
  <div class="about-photo" role="img" aria-label="Portrait of the attorney"></div>
  <div class="badge" aria-hidden="true"></div>
  <h2 class="h2" style="left:515px;top:1088px">ABOUT ME</h2>
  <div class="kicker" style="left:515px;top:1150px">Who Am I <i></i></div>
  <p class="para" style="left:515px;top:1218px;width:532px">Dolores is a graduate of Eastbridge University in Boston, Massachusetts. She received her Bachelors of Science degree in Criminal Justice and a minor in Political Science in 1993. While attending Eastbridge, Dolores was a Marden Foundation Scholar, graduating from the University Magna Cum Laude. Dolores obtained her Juris Doctor from Harrow Point Law School in Boston, Massachusetts in 1999. During her law school career, she interned at the Department of Environmental Protection in Boston, Massachusetts.</p>
  <a class="btn btn-solid" style="left:510px;top:1430px;height:40px;font-size:14px">KNOW MORE <svg viewBox="0 0 12 12" fill="none" stroke="#fff" stroke-width="1.5"><path d="M2 10L10 2M4 2h6v6"/></svg></a>
</section>

<div class="pale-band"></div>
<section class="consult">
  <div class="consult-arc" style="left:-120px;top:-180px;width:420px;height:420px"></div>
  <div class="consult-arc" style="left:820px;top:120px;width:380px;height:380px"></div>
  <h3>FREE 30-MINUTE CONSULTATION</h3>
  <p>I respect the fact that your time is valuable. Therefore, I provide a free 30 minute consultation to potential clients. The consultation is a great way to learn more about what options there are for your issue, as well as for both you and I to see if we are a good fit.</p>
  <a class="btn btn-ghost" style="left:443px;top:237px;height:44px">CONTACT ME <svg viewBox="0 0 12 12" fill="none" stroke="#fff" stroke-width="1.5"><path d="M2 10L10 2M4 2h6v6"/></svg></a>
</section>

<section class="family">
  <h2 class="h2 h2-sm" style="left:110px;top:2026px">FAMILY LAW</h2>
  <div class="kicker" style="left:110px;top:2096px;font-size:15px">Why Hiring an Attorney is the Right Choice</div>
  <p class="para" style="left:110px;top:2137px;width:575px">Going through a divorce is difficult. Especially in cases where there are minor children or complicated financial holdings, questions will arise that you may not be prepared to answer without the assistance of a knowledgeable and reputable advocate. Some of the questions that may arise are, will one party remain in the family home or will it be sold? Who will be the primary caretaker of the children? How will custody decisions be affected if one party moves to a different town or state?</p>
  <a class="btn btn-solid" style="left:110px;top:2308px;height:40px;font-size:14px">KNOW MORE <svg viewBox="0 0 12 12" fill="none" stroke="#fff" stroke-width="1.5"><path d="M2 10L10 2M4 2h6v6"/></svg></a>
  <div class="photo-ring" style="left:742px;top:2027px;width:350px;height:350px"></div>
  <div class="photo-fill family-fill" style="left:756px;top:2041px;width:322px;height:322px" role="img" aria-label="Photo of a family law sourcebook cover"></div>
</section>

<section class="services">
  <div class="service" style="left:35px"><span class="service-icon"><svg width="38" height="38" viewBox="0 0 24 24" fill="none" stroke="#1e2b3a" stroke-width="1.5"><rect x="5" y="3" width="14" height="18" rx="1"/><path d="M8 8h8M8 12h8M8 16h5"/></svg></span>Pre and Post Nuptial Agreements</div>
  <div class="service" style="left:419px"><span class="service-icon"><svg width="38" height="38" viewBox="0 0 24 24" fill="none" stroke="#1e2b3a" stroke-width="1.5"><rect x="4" y="3" width="13" height="18" rx="1"/><path d="M10.5 10l-2-2a1.4 1.4 0 012-2 1.4 1.4 0 012 2zM7 15h7M7 18h5M20 5v13l-1 2-1-2V5z"/></svg></span>Divorce</div>
  <div class="service" style="left:624px"><span class="service-icon"><svg width="38" height="38" viewBox="0 0 24 24" fill="none" stroke="#1e2b3a" stroke-width="1.5"><rect x="3" y="4" width="8" height="16"/><rect x="13" y="4" width="8" height="16"/><path d="M5 8h4M5 11h4M15 8h4M15 11h4"/></svg></span>Post-Divorce</div>
</section>

<section class="estate">
  <div class="photo-ring" style="left:95px;top:2720px;width:354px;height:354px"></div>
  <div class="photo-fill estate-fill" style="left:109px;top:2734px;width:326px;height:326px" role="img" aria-label="Photo of estate planning reference books on a desk"></div>
  <h2 class="h2 h2-sm" style="left:494px;top:2734px">ESTATE PLANNING</h2>
  <div class="abs" style="left:494px;top:2790px;width:50px;height:2px;background:var(--green)"></div>
  <p class="para" style="left:497px;top:2816px;width:572px">Whether you are creating an estate plan for the first time or updating your existing plan, I strive to make the estate planning process easy to understand, comfortable and comprehensive.</p>
  <p class="para" style="left:497px;top:2911px;width:572px">Throughout the process of drafting an estate plan, additional professionals such as a financial planner, CPA and life insurance agent may become necessary resources in the handling of your assets. If this is necessary, I will advise you accordingly and provide you with a list of knowledgeable professionals to choose from.</p>
  <a class="btn btn-solid" style="left:494px;top:3044px;height:40px;font-size:14px">KNOW MORE <svg viewBox="0 0 12 12" fill="none" stroke="#fff" stroke-width="1.5"><path d="M2 10L10 2M4 2h6v6"/></svg></a>
</section>

<section class="estate-card">
  <div class="doc" style="left:84px;top:77px"><span class="doc-icon"><svg width="20" height="20" viewBox="0 0 24 24" fill="none" stroke="#fff" stroke-width="1.8"><rect x="5" y="3" width="14" height="18" rx="1"/><path d="M8 8h8M8 12h8M8 16h5"/></svg></span>Will</div>
  <div class="doc" style="left:84px;top:127px"><span class="doc-icon"><svg width="20" height="20" viewBox="0 0 24 24" fill="none" stroke="#fff" stroke-width="1.8"><rect x="5" y="3" width="14" height="18" rx="1"/><path d="M8 8h8M8 12h8M8 16h5"/></svg></span>Durable Power of Attorney<br>with Nomination of Guardian</div>
  <div class="doc" style="left:84px;top:176px"><span class="doc-icon"><svg width="20" height="20" viewBox="0 0 24 24" fill="none" stroke="#fff" stroke-width="1.8"><rect x="5" y="3" width="14" height="18" rx="1"/><path d="M8 8h8M8 12h8M8 16h5"/></svg></span>Health Care Proxy</div>
  <div class="doc" style="left:346px;top:77px"><span class="doc-icon"><svg width="20" height="20" viewBox="0 0 24 24" fill="none" stroke="#fff" stroke-width="1.8"><rect x="5" y="3" width="14" height="18" rx="1"/><path d="M8 8h8M8 12h8M8 16h5"/></svg></span>Memorandum of Remains</div>
  <div class="doc" style="left:346px;top:127px"><span class="doc-icon"><svg width="20" height="20" viewBox="0 0 24 24" fill="none" stroke="#fff" stroke-width="1.8"><rect x="5" y="3" width="14" height="18" rx="1"/><path d="M8 8h8M8 12h8M8 16h5"/></svg></span>Revocable Living Trust</div>
  <div class="doc" style="left:346px;top:176px"><span class="doc-icon"><svg width="20" height="20" viewBox="0 0 24 24" fill="none" stroke="#fff" stroke-width="1.8"><rect x="5" y="3" width="14" height="18" rx="1"/><path d="M8 8h8M8 12h8M8 16h5"/></svg></span>Irrevocable Living Trust</div>
  <div class="doc" style="left:620px;top:77px"><span class="doc-icon"><svg width="20" height="20" viewBox="0 0 24 24" fill="none" stroke="#fff" stroke-width="1.8"><rect x="5" y="3" width="14" height="18" rx="1"/><path d="M8 8h8M8 12h8M8 16h5"/></svg></span>Trustee's Certificate</div>
  <div class="doc" style="left:620px;top:127px"><span class="doc-icon"><svg width="20" height="20" viewBox="0 0 24 24" fill="none" stroke="#fff" stroke-width="1.8"><rect x="5" y="3" width="14" height="18" rx="1"/><path d="M8 8h8M8 12h8M8 16h5"/></svg></span>Quitclaim Deed</div>
  <div class="doc" style="left:620px;top:176px"><span class="doc-icon"><svg width="20" height="20" viewBox="0 0 24 24" fill="none" stroke="#fff" stroke-width="1.8"><rect x="5" y="3" width="14" height="18" rx="1"/><path d="M8 8h8M8 12h8M8 16h5"/></svg></span>Trust Amendments</div>
</section>

<section class="faq">
  <h2 class="h2" style="left:67px;top:3584px;font-size:48px">FAQ</h2>
  <div class="faq-q open" style="top:3709px"><span class="num">01</span>What will a divorce cost me?<span class="faq-toggle"><svg width="16" height="16" viewBox="0 0 16 16"><path d="M4.5 8h7" stroke="#fff" stroke-width="1.6"/></svg></span></div>
  <p class="faq-answer">I currently bill my family law clients at <em>$385.00 per hour.</em> Although I will make every effort to keep costs reasonable for you and work within the agreed upon retainer, I cannot give you a fixed price for a divorce (or any other family law matter). The reason is because I cannot predict what the opposition will file during the litigation process, or what pleadings I may need to file on your behalf in order to achieve your goals in this matter.</p>
  <div class="faq-line" style="top:3884px"></div>
  <div class="faq-q" style="top:3911px"><span class="num">02</span>How long will it take for me to get divorced?<span class="faq-toggle"><svg width="16" height="16" viewBox="0 0 16 16"><path d="M4.5 8h7M8 4.5v7" stroke="#fff" stroke-width="1.6"/></svg></span></div>
  <div class="faq-line" style="top:3946px"></div>
  <div class="faq-q" style="top:3973px"><span class="num">03</span>What kinds of information should I bring with me for my free 30-minute<br><span style="margin-left:27px">consultation?</span><span class="faq-toggle"><svg width="16" height="16" viewBox="0 0 16 16"><path d="M4.5 8h7M8 4.5v7" stroke="#fff" stroke-width="1.6"/></svg></span></div>
  <div class="faq-line" style="top:4026px"></div>
  <div class="faq-back"></div>
  <div class="faq-photo" role="img" aria-label="Black and white portrait of the attorney"></div>
</section>

<svg class="contact-wave" width="1200" height="622" viewBox="0 0 1200 622">
  <path d="M0 60 Q600 -40 1200 60 L1200 622 L0 622Z" fill="#e9c2a8"/>
  <path d="M0 80 Q600 -10 1200 80 L1200 622 L0 622Z" fill="#1e2b3a"/>
</svg>
<section class="contact-box">
  <div class="contact-photo" role="img" aria-label="Photo of the law office building exterior with trees"></div>
  <h2>CONTACT</h2>
  <div class="field" style="left:502px;top:139px;width:248px;height:42px">Your Name</div>
  <div class="field" style="left:771px;top:139px;width:245px;height:42px">Phone Number</div>
  <div class="field" style="left:502px;top:196px;width:514px;height:43px">Email Address</div>
  <div class="field" style="left:502px;top:253px;width:514px;height:85px">Message</div>
  <a class="btn btn-solid" style="left:502px;top:364px;height:40px;font-size:14px;padding:0 28px">SUBMIT <svg viewBox="0 0 12 12" fill="none" stroke="#fff" stroke-width="1.5"><path d="M2 10L10 2M4 2h6v6"/></svg></a>
</section>

<footer>
  <h4 class="footer-title" style="left:232px;top:4668px">QUICK LINKS</h4>
  <ul class="footer-links"><li>About</li><li>Family Law</li><li>Estate Planning</li><li>Location</li><li>Contact</li></ul>
  <div class="footer-brand"><div class="footer-mark"></div><p>Dolores Quintana<br>Attorney at Law</p></div>
  <h4 class="footer-title" style="left:833px;top:4668px">CONTACT US</h4>
  <div class="fcontact" style="top:4728px"><span class="fcontact-icon"><svg width="12" height="12" viewBox="0 0 24 24" fill="none" stroke="#fff" stroke-width="2"><path d="M5 3h4l2 5-3 2a12 12 0 006 6l2-3 5 2v4a2 2 0 01-2 2A18 18 0 013 5a2 2 0 012-2z"/></svg></span><span>CALL US : 555-014-2290<br>FAX US : 555-014-2291</span></div>
  <div class="fcontact" style="top:4778px"><span class="fcontact-icon"><svg width="12" height="12" viewBox="0 0 24 24" fill="none" stroke="#fff" stroke-width="2"><rect x="3" y="5" width="18" height="14"/><path d="M3 5l9 8 9-8"/></svg></span><span>EMAIL US<br>dquintana@quintanamail.com</span></div>
  <div class="fcontact" style="top:4823px"><span class="fcontact-icon"><svg width="12" height="12" viewBox="0 0 24 24" fill="none" stroke="#fff" stroke-width="2"><path d="M12 22s7-7 7-12a7 7 0 00-14 0c0 5 7 12 7 12z"/><circle cx="12" cy="10" r="2.5"/></svg></span><span>42 Linden Street<br>Harborview, MA 01999</span></div>
  <div class="footer-rule"></div>
  <p class="copyright">Copyright © 2025 All Rights Reserved By Company name</p>
</footer>

</body>
</html>
```